Clear Plastic Card Design

I am looking to have a business card designed from my logo icon. I am looking to match the style of a different business card I have attached in the files.
Looking for a card that is plastic, with layers of transparency in the shape of my logo icon (also attached in the files) - not a circle like the other card. The winning design will incorporate the red icon logo on the front and back and include the charity's name, "Light for the Weary Souls" in the same or similar font, as well as an email and phone number. For now, use the email: email@lightfortheweary-mail.org and the phone number 555-382-7194.
We like how the sample business card has transparency, partial and full opacity layers and a matching color scheme. Files will need to be in vector so that our business card printing company can work with it.
UPDATE:
We've some excellent designs in, thank you everyone! I got an early review from the owner, and he requested a minor redirect to find his perfect design. He wants the design to stand out by NOT being a rectangle. Try instead a circle, square, or best yet - something that falls in the outline of the logo icon, either fully or partially. Thank you, everyone!
Light for the Weary Souls text should be incorporated as well as a phone and email.

```html
<!DOCTYPE html>
<html lang="en">
<head>
<meta charset="utf-8">
<title>Light for the Weary Souls – Round Business Card</title>
<link rel="stylesheet" href="https://fonts.googleapis.com/css2?family=Bebas+Neue&family=Quicksand:wght@500&display=swap">
<style>
  :root {
    --backdrop: #e9e6e2;
    --card: #333333;
    --card-rim: #222222;
    --accent: #e8470f;
    --ink: #ffffff;
  }
  html, body {
    margin: 0;
    padding: 0;
    width: 1200px;
    height: 800px;
    overflow: hidden;
    background: var(--backdrop);
  }
  .stage {
    display: block;
    width: 1200px;
    height: 800px;
  }
  .card-rim { fill: var(--card-rim); }
  .card-face { fill: var(--card); }
  .brand-name {
    font-family: "Quicksand", sans-serif;
    font-weight: 500;
    fill: var(--ink);
  }
  .brand-dot { fill: var(--accent); }
  .icon-tile { fill: var(--accent); }
  .icon-glyph { fill: none; stroke: var(--ink); stroke-width: 2.4; stroke-linecap: round; stroke-linejoin: round; }
  .contact-phone {
    font-family: "Bebas Neue", sans-serif;
    font-size: 38px;
    fill: var(--ink);
  }
  .contact-email {
    font-family: "Bebas Neue", sans-serif;
    font-size: 24px;
    letter-spacing: 0.5px;
    fill: var(--ink);
    text-transform: uppercase;
  }
  .name-band { fill: var(--accent); }
  .name-band-text {
    font-family: "Bebas Neue", sans-serif;
    font-size: 38px;
    fill: var(--ink);
  }
</style>
</head>
<body>
<svg class="stage" viewBox="0 0 1200 800" xmlns="http://www.w3.org/2000/svg">
  <defs>
    <clipPath id="back-face-clip">
      <circle cx="852" cy="444" r="224"/>
    </clipPath>
  </defs>

  <!-- Front of card -->
  <g class="card card--front">
    <circle class="card-rim" cx="348" cy="444" r="238"/>
    <circle class="card-face" cx="348" cy="444" r="224"/>
    <circle class="brand-dot" cx="452" cy="420" r="34"/>
    <text class="brand-name" x="406" y="425" font-size="34" text-anchor="end">Light for the</text>
    <text class="brand-name" x="406" y="465" font-size="34" text-anchor="end">Weary Souls</text>
  </g>

  <!-- Back of card -->
  <g class="card card--back">
    <circle class="card-rim" cx="852" cy="444" r="238"/>
    <circle class="card-face" cx="852" cy="444" r="224"/>

    <circle class="brand-dot" cx="900" cy="332" r="24"/>
    <text class="brand-name" x="866" y="338" font-size="20" text-anchor="end">Light for the</text>
    <text class="brand-name" x="866" y="360" font-size="20" text-anchor="end">Weary Souls</text>

    <g class="contact contact--phone">
      <rect class="icon-tile" x="664" y="408" width="40" height="40" rx="10"/>
      <path class="icon-glyph" d="M676 418 l5 -2 l4 7 l-3 3 q2 5 7 7 l3 -3 l7 4 l-2 5 q-12 1 -21 -21 z"/>
      <text class="contact-phone" x="718" y="446">555-382-7194</text>
    </g>

    <g class="contact contact--email">
      <rect class="icon-tile" x="664" y="461" width="40" height="40" rx="10"/>
      <rect class="icon-glyph" x="673" y="472" width="22" height="16" rx="2"/>
      <path class="icon-glyph" d="M673 474 l11 8 l11 -8"/>
      <text class="contact-email" x="718" y="490">email@lightfortheweary-mail.org</text>
    </g>

    <g clip-path="url(#back-face-clip)">
      <polygon class="name-band" points="644,526 1062,526 1046,584 652,584"/>
      <text class="name-band-text" x="674" y="568">LIGHT FOR THE WEARY SOULS</text>
    </g>
  </g>
</svg>
</body>
</html>
```